Norvane Website Design (New Start Up Investment Management Firm)

We need a website designed. We have attached a Powerpoint with our proposed website content (which is quite minimal), the format is just a suggestion but we would like to see your alternative and improved ideas. We are a boutique investment firm so are looking for something sleek and professional. I have included on the last page of the attachment our brand colours and font styles as well as attaching our logo design. We would like the successful designer to design the website and build the buttons etc.

On the "Contact Us" page, we are open to suggestions on how best to show the map, whether is should be static or open a google maps page. We would like the phone number and email address to be set up so people can click on them on their phone and it calls us or emails us directly.

We would prefer not to have photos of landscapes on the site.
Our website is hosted on a Linux based website.

We would also like 3 links at the bottom of each page for links to pdfs:
- Disclaimer, Terms and Conditions of Web Site Use
- Stewardship
- Pillar III

Target Market(s)

Institutional Investors

Industry/Entity Type

Investment

Coding

Coded - Design and coding required

Number of Pages Required

3 page

Font styles to use
Other font styles liked:
• Logo: Lato, Text: Source Sans Pro

Colors

Designer to choose colors to be used in the design.

Requirements
Must have
• The website must use the colours and fonts on the last page of the attached powerpoint. I can't see an option to select the exact colour palette below so please look at the PPT.
• For others please see Project description.
Should not have
• Landscape photos

```html
<!DOCTYPE html>
<html lang="en">
<head>
<meta charset="utf-8">
<title>Norvane Investment Management</title>
<link href="https://fonts.googleapis.com/css2?family=Lato:wght@400;700&display=swap" rel="stylesheet">
<style>
:root{
  --navy:#002d62;
  --royal:#003da5;
  --sky:#6ab4e8;
  --sky-text:#5aace6;
  --card:#eef0f8;
  --card-line:#dde0ec;
  --ink:#1c1c1c;
  --body:#333;
  --white:#fff;
}
*{margin:0;padding:0;box-sizing:border-box}
html,body{width:1200px;height:1073px;overflow:hidden;background:var(--white)}
body{position:relative;font-family:'Lato',sans-serif;color:var(--body)}
.abs{position:absolute}

/* header */
.brand{left:99px;top:26px;display:flex;align-items:center;gap:10px;white-space:nowrap}
.brand-mark{width:44px;height:44px;background:var(--navy);flex:none}
.brand-name{font-size:31px;font-weight:400;color:var(--navy);line-height:1;letter-spacing:1px}
.brand-sub{font-size:7.5px;letter-spacing:1.5px;color:var(--navy);margin-top:3px}
.nav{top:44px;left:0;font-size:13px;color:var(--royal)}
.nav a{position:absolute;white-space:nowrap;text-decoration:none;color:var(--royal)}
.nav a.home{color:var(--ink)}
.nav .divider{position:absolute;left:1066px;top:-1px;width:1px;height:17px;background:#ccc}
.search{left:1088px;top:44px}

/* tiles */
.tile{left:99px;width:314px;height:134px;overflow:hidden;color:var(--white);display:flex;align-items:center}
.tile.light{background:var(--sky)}
.tile.deep{background:var(--royal)}
.tile .icon{position:absolute;left:18px;top:50%;transform:translateY(-50%)}
.tile h2{margin-left:78px;font-size:20px;font-weight:400;line-height:34px;white-space:nowrap}
.corner{position:absolute;right:0;bottom:0;width:56px;height:56px}
.corner::before{content:"";position:absolute;inset:0;clip-path:polygon(100% 0,100% 100%,0 100%)}
.corner.deep::before{background:var(--royal)}
.corner.light::before{background:var(--sky)}
.corner.navy::before{background:var(--navy)}
.corner span{position:absolute;right:10px;bottom:6px;font-size:20px;font-weight:700;color:var(--white);line-height:1}

/* hero */
.hero{left:429px;top:100px;width:673px;height:433px;background:var(--navy);color:var(--white);padding:50px 0 0 47px}
.hero h1{font-size:23px;font-weight:700;letter-spacing:.2px}
.hero .lead{margin-top:20px;font-size:19px;line-height:28.3px;color:var(--sky-text);white-space:nowrap}
.hero .copy{margin-top:26px;font-size:13px;line-height:24.9px;white-space:nowrap}

/* lower cards */
.news{left:99px;top:555px;width:314px;height:396px;border:1px solid var(--card-line);padding:31px 25px 0 25px}
.news h3{font-size:18px;font-weight:700;color:var(--navy)}
.item{margin-top:24px}
.item + .item{margin-top:36px}
.item h4{font-size:17px;font-weight:400;color:var(--ink);margin-left:1px}
.item p{margin-top:11px;font-size:13px;line-height:25px;margin-left:1px}
.item time{display:block;margin-top:9px;font-size:13px;color:var(--sky-text);margin-left:1px}
.service{top:555px;width:217px;height:396px;background:var(--card);border:1px solid var(--card-line);padding:32px 23px 0 23px}
.service h3{font-size:18px;font-weight:400;color:var(--navy)}
.service p{margin-top:17px;font-size:13px;line-height:25.7px}
.service .art{position:absolute;left:23px;top:252px;width:98px;height:98px;border-radius:6px}

/* footer */
.footer{left:0;top:978px;width:1200px;height:95px;background:var(--navy);color:var(--white)}
.footer .brand{left:99px;top:24px}
.footer .brand-mark{background:var(--white);width:48px;height:48px}
.footer .brand-name,.footer .brand-sub{color:var(--white)}
.footer .brand-name{font-size:33px}
.footer .brand-sub{font-size:8px}
.footer .rule{left:344px;top:27px;width:1px;height:52px;background:#5d7596}
.footer .legal{left:366px;top:28px;font-size:13px;line-height:29px;white-space:nowrap}
.social{left:961px;top:37px;display:flex;gap:16px}
.social i{display:block;width:16px;height:16px;border-radius:50%;background:var(--white)}
</style>
</head>
<body>

<header>
  <div class="abs brand">
    <div class="brand-mark"></div>
    <div>
      <div class="brand-name">NORVANE</div>
      <div class="brand-sub">INVESTMENT MANAGEMENT</div>
    </div>
  </div>
  <nav class="abs nav">
    <a class="home" href="#" style="left:487px">HOME</a>
    <a href="#" style="left:573px">ABOUT NORVANE</a>
    <a href="#" style="left:712px">OUR APPROACH AND PHILOSOPHY</a>
    <a href="#" style="left:956px">CONTACT US</a>
    <span class="divider"></span>
  </nav>
  <svg class="abs search" width="14" height="14" viewBox="0 0 14 14" aria-label="Search">
    <circle cx="5.5" cy="5.5" r="4.2" fill="none" stroke="#003da5" stroke-width="2.2"/>
    <line x1="8.6" y1="8.6" x2="12.8" y2="12.8" stroke="#003da5" stroke-width="2.6" stroke-linecap="round"/>
  </svg>
</header>

<a class="abs tile light" style="top:100px">
  <svg class="icon" width="36" height="36" viewBox="0 0 36 36"><circle cx="18" cy="18" r="18" fill="#9fd0f2"/><circle cx="18" cy="10" r="3" fill="#6ab4e8"/><rect x="15" y="15" width="6" height="13" rx="1" fill="#6ab4e8"/></svg>
  <h2>ABOUT NORVANE</h2>
  <span class="corner deep"><span>+</span></span>
</a>
<a class="abs tile deep" style="top:250px">
  <svg class="icon" width="48" height="36" viewBox="0 0 48 36"><g fill="#6ab4e8"><rect x="0" y="0" width="2.5" height="36"/><rect x="0" y="33.5" width="48" height="2.5"/><rect x="8" y="20" width="4" height="11"/><rect x="15" y="12" width="4" height="19"/><rect x="22" y="17" width="4" height="14"/><rect x="29" y="9" width="4" height="22"/><rect x="36" y="5" width="4" height="26"/></g></svg>
  <h2>OUR APPROACH<br>AND PHILOSOPHY</h2>
  <span class="corner light"><span>+</span></span>
</a>
<a class="abs tile deep" style="top:399px">
  <svg class="icon" width="34" height="34" viewBox="0 0 34 34"><path d="M7 1 L12 9 L9 13 C11 19 15 23 21 25 L25 22 L33 27 L29 33 C14 32 2 20 1 5 Z" fill="#6ab4e8"/></svg>
  <h2>CONTACT US</h2>
  <span class="corner light"><span>+</span></span>
</a>

<section class="abs hero">
  <h1>ABOUT NORVANE</h1>
  <p class="lead">Norvane Investment Management<br>wasfounded in 2016 with a clear vision<br>to create an independent and nimble<br>firm focused on generating superior<br>risk-adjusted returns.</p>
  <p class="copy">Norvane has designed an innovative investment approach which aims<br>to harness the best elements of alternative investment management<br>whilst reducing its recognised shortcomings. We are a performance<br>and client focused firm, committed to building lasting relationships,<br>treating our clients like partners rather than revenue streams.</p>
</section>

<section class="abs news">
  <h3>NEWS</h3>
  <article class="item">
    <h4>At vereos et accus amtusdio.</h4>
    <p>At vero eos et accusamus et iusto odio diiss imos ducimus qui blanditiis praesentiumero eos et accusamus et iusto odio.</p>
    <time>Apr 21, 2017</time>
  </article>
  <article class="item">
    <h4>At vereos et accus amtusdio.</h4>
    <p>At vero eos et accusamus et iusto odio diiss imos ducimus qui blanditiis praesentiumero eos et accusamus et iusto odio.</p>
    <time>Apr 21, 2017</time>
  </article>
  <span class="corner navy"><span>+</span></span>
</section>

<section class="abs service" style="left:429px">
  <h3>Financial Markets</h3>
  <p>At vero eos et accusa lomusu sto odio dignissimos ducims qui blanditiis praesentiumou ptatum deleniti atque corruti quos dolores.</p>
  <div class="art" role="img" aria-label="Icon of a rising bar chart with a dollar sign" style="background:var(--royal)"></div>
</section>
<section class="abs service" style="left:657px">
  <h3>Investment</h3>
  <p>At vero eos et accusa lomusu sto odio dignissimos ducims qui blanditiis praesentiumou ptatum deleniti atque corruti quos dolores.</p>
  <div class="art" role="img" aria-label="Icon of a hand holding a dollar sign" style="background:var(--royal)"></div>
</section>
<section class="abs service" style="left:885px">
  <h3>Planning &amp; Analysis</h3>
  <p>At vero eos et accusa lomusu sto odio dignissimos ducims qui blanditiis praesentiumou ptatum deleniti atque corruti quos dolores.</p>
  <div class="art" role="img" aria-label="Icon of a monitor with a chart and magnifying glass" style="background:var(--sky)"></div>
</section>

<footer class="abs footer">
  <div class="abs brand">
    <div class="brand-mark"></div>
    <div>
      <div class="brand-name">NORVANE</div>
      <div class="brand-sub">INVESTMENT MANAGEMENT</div>
    </div>
  </div>
  <span class="abs rule"></span>
  <div class="abs legal">© 2017 Norvane. All Copyrights are reserved.<br>Disclaimer, Terms and Conditions,&nbsp; Stewardship,&nbsp; Pillar III</div>
  <div class="abs social" aria-label="Social links"><i></i><i></i><i></i><i></i><i></i></div>
</footer>

</body>
</html>
```